Homepage for the brisk-find Web Application

At the end of this text, you will find a link to a website that is under construction for a webApp that I intend to launch soon. The contest goal is for you to make redesign the homepage in a nice, fresh, modern Style. Only design, no coding necessary. It needs to have a responsive version for small screens like smart phones. Attached is the text for it, and some images that you may use. You are welcome to find or create additional supporting images. You can use PixTrove.example or similar service to find new images as long as I can purchase the non-exclusive use rights for the images at similar prices. The contest is just for the home page. However, the winner, if I like the work and we can agree on a fair price, could be contracted on a one-on-one basis to do the rest of the site. You are welcome to suggest minor changes like font sizes and minor variations on the Header banner, but that banner is consistent with the user interface of the application therefore should not change too much. The information should flow somewhat continually without much use of side bars or things like that.
https://www.brisk-find.example
Sincerely,
Marco D. Ferral

```html
<!DOCTYPE html>
<html lang="en">
<head>
<meta charset="utf-8">
<title>Brisk Find – Home</title>
<link href="https://fonts.googleapis.com/css2?family=Montserrat:ital,wght@0,400;0,500;0,600;0,700;0,800;1,300;1,400&family=Open+Sans:wght@400;600;700&display=swap" rel="stylesheet">
<style>
:root{
  --orange:#ff7b5a;
  --orange-dark:#f2643f;
  --blue:#1f8fdc;
  --blue-deep:#0f5fae;
  --blue-light:#39b4ee;
  --teal:#22b3c7;
  --ink:#1f2a3a;
  --text:#5d6673;
  --muted:#9aa3ad;
  --white:#ffffff;
  --paper:#f3f4f6;
}
*{box-sizing:border-box;margin:0;padding:0}
html,body{width:1200px;height:4660px;overflow:hidden}
body{font-family:"Open Sans",Arial,sans-serif;color:var(--text);background:var(--white);font-size:14px}
h1,h2,h3,h4,.btn{font-family:"Montserrat",Arial,sans-serif}
section,header,footer{position:relative;width:1200px;overflow:hidden}
.btn{display:inline-block;border-radius:22px;font-weight:700;font-size:12px;letter-spacing:.5px;text-transform:uppercase;padding:11px 26px;color:var(--white);background:var(--orange);text-decoration:none}
.btn-blue{background:var(--blue)}
.btn-ghost{background:transparent;border:2px solid var(--white)}
.section-title{font-size:34px;font-weight:700;color:var(--ink);text-align:center}
.section-sub{text-align:center;font-size:13px;line-height:1.6;max-width:560px;margin:10px auto 0}
.rule{width:60px;height:3px;background:var(--ink);margin:12px auto 0}
.placeholder{display:block}

/* header */
.site-header{height:128px;background:var(--white);padding:0 60px}
.logo{position:absolute;left:60px;top:34px;display:flex;align-items:center;gap:12px;font-family:"Montserrat",sans-serif;font-weight:800;font-size:42px;color:var(--teal)}
.logo-dot{width:22px;height:22px;border-radius:50%;background:var(--teal)}
.topbar{position:absolute;right:60px;top:26px;display:flex;align-items:center;gap:22px;font-size:12px;color:var(--text)}
.topbar .login{color:var(--ink);font-weight:600}
.topbar .btn{padding:8px 20px;border-radius:6px}
.nav{position:absolute;right:60px;top:80px;display:flex;gap:30px;font-family:"Montserrat",sans-serif;font-weight:600;font-size:13px;color:var(--ink)}
.nav .active{color:var(--orange)}

/* hero */
.hero{height:532px;background:linear-gradient(120deg,var(--blue-light),var(--blue) 55%,var(--blue-deep))}
.hero-art{position:absolute;left:70px;top:30px;width:500px;height:470px;border-radius:12px;background:linear-gradient(160deg,#5fd2d4,#2ea0c9 60%,#1d6fae)}
.hero-copy{position:absolute;left:630px;top:120px;width:520px;color:var(--white)}
.hero-copy .lead{font-family:"Montserrat",sans-serif;font-style:italic;font-weight:300;font-size:38px}
.hero-copy h1{font-size:44px;font-weight:800;line-height:1.08;text-transform:uppercase;margin-top:6px}
.hero-copy .accent{font-family:"Montserrat",sans-serif;font-size:38px;color:var(--orange);font-weight:500;margin-top:6px}
.hero-actions{display:flex;gap:30px;margin-top:40px}
.hero-actions .btn{font-size:15px;text-transform:none;padding:14px 40px;border-radius:6px;font-weight:500}

/* welcome */
.welcome{height:500px;text-align:center;padding-top:32px}
.eyebrow{font-family:"Montserrat",sans-serif;font-size:11px;font-weight:600;color:var(--orange);letter-spacing:1px;text-transform:uppercase}
.welcome h2{font-size:34px;color:var(--ink);font-weight:700;margin-top:10px}
.welcome p{width:1040px;margin:48px auto 0;text-align:left;font-size:13px;line-height:1.75}
.welcome .btn{margin-top:60px}

/* pricing */
.pricing{height:560px;background:var(--orange);padding-top:60px}
.pricing .section-title,.pricing .section-sub{color:var(--white)}
.plans{display:flex;justify-content:center;gap:72px;margin-top:46px}
.plan{width:200px;height:290px;background:var(--white);border-radius:4px;box-shadow:0 10px 24px rgba(0,0,0,.14);text-align:center;padding-top:38px}
.plan h3{font-size:13px;font-weight:600;color:var(--ink)}
.price{font-family:"Montserrat",sans-serif;font-weight:700;color:var(--blue-deep);font-size:62px;margin-top:14px;line-height:1}
.price sup{font-size:26px;vertical-align:top;position:relative;top:10px}
.plan p{font-size:11px;line-height:1.5;margin:14px 18px 0;color:var(--muted)}
.plan .btn{margin-top:26px;padding:9px 20px;font-size:10px;text-transform:none}

/* blog */
.blog{height:640px;padding-top:62px}
.posts{display:flex;justify-content:center;gap:42px;margin-top:30px}
.post{width:292px}
.post-img{width:292px;height:186px}
.post .meta{font-size:10px;color:var(--muted);margin-top:26px}
.post h3{font-size:17px;line-height:1.3;color:var(--orange);font-weight:700;margin-top:12px}
.post p{font-size:11px;line-height:1.6;margin-top:12px}
.post .btn{margin-top:18px;padding:7px 18px;font-size:9px}

/* app */
.app{height:360px;background:linear-gradient(100deg,var(--blue-deep),var(--blue) 60%,var(--blue-light))}
.app-copy{position:absolute;left:140px;top:96px;width:620px;color:var(--white)}
.app-copy h2{font-size:34px;font-weight:700}
.app-copy p{font-size:12px;line-height:1.65;margin-top:18px;opacity:.92}
.stores{display:flex;gap:16px;margin-top:28px}
.stores .btn{border-radius:6px;padding:10px 16px;font-size:10px;display:flex;align-items:center;gap:8px}
.stores .btn-ghost{border-width:1px}
.store-dot{width:12px;height:12px;border-radius:3px;background:var(--white)}
.app-art{position:absolute;left:860px;top:40px;width:230px;height:300px;border-radius:24px;background:linear-gradient(150deg,#bfe9ff,#6fc3f0 50%,var(--orange))}

/* reviews */
.reviews{height:480px;padding-top:46px;text-align:center}
.avatar{width:64px;height:64px;border-radius:50%;background:linear-gradient(135deg,#c9ced6,#7d8794);margin:38px auto 0}
.reviewer{font-family:"Montserrat",sans-serif;font-size:24px;font-weight:700;color:var(--blue-deep);margin-top:10px}
.stars{display:flex;justify-content:center;gap:3px;margin-top:6px}
.quote{width:600px;margin:16px auto 0;font-size:12px;line-height:1.65}
.arrow{position:absolute;top:236px}
.dots{display:flex;justify-content:center;gap:8px;margin-top:30px}
.dots span{width:7px;height:7px;border-radius:50%;background:#c9ced6}
.dots span.on{background:var(--ink)}

/* faq */
.faq{height:660px;background:var(--orange);padding-top:104px}
.faq .section-title{color:var(--white)}
.faq .rule{background:var(--white)}
.faq-grid{display:flex;gap:40px;margin:64px 0 0 60px}
.faq-col{width:500px;display:flex;flex-direction:column;gap:16px}
.faq-item{height:40px;border:1px solid rgba(255,255,255,.75);display:flex;align-items:center;justify-content:space-between;padding:0 16px;color:var(--white);font-family:"Montserrat",sans-serif;font-size:13px;font-weight:500;background:rgba(255,255,255,.06)}
.faq-open{background:var(--blue);border:1px solid var(--blue);padding:14px 16px 18px;color:var(--white)}
.faq-open h4{font-size:13px;font-weight:500;display:flex;justify-content:space-between}
.faq-open p{font-size:11px;line-height:1.65;margin-top:14px;opacity:.95}

/* contact */
.contact{height:560px;background:var(--paper);padding-top:70px}
.form{display:flex;gap:40px;width:700px;margin:40px auto 0}
.form-col{width:330px;display:flex;flex-direction:column;gap:18px}
.field label{display:block;font-size:11px;color:var(--text)}
.field .line{height:30px;border-bottom:1px solid #d4d8dd}
.field .area{height:130px;border:1px solid #d4d8dd;margin-top:6px;background:var(--white)}
.contact .send{display:block;width:max-content;margin:50px auto 0;padding:10px 26px;font-size:11px}

/* footer */
.site-footer{height:240px;background:linear-gradient(100deg,var(--blue-deep),var(--blue) 60%,var(--blue-light));text-align:center;padding-top:70px;color:var(--white)}
.social{display:flex;justify-content:center;gap:18px}
.social span{width:42px;height:42px;border:1px solid rgba(255,255,255,.8);border-radius:50%}
.copyright{font-size:11px;margin-top:50px;opacity:.9}
</style>
</head>
<body>

<header class="site-header">
  <div class="logo"><span class="logo-dot"></span>Brisk Find</div>
  <div class="topbar">
    <span>Call Us: +1 555 013 2468</span>
    <span>Mail: hello@briskfind.example</span>
    <span class="login">Login</span>
    <span class="btn">Free Trial</span>
  </div>
  <nav class="nav">
    <span class="active">Home</span><span>About Us</span><span>Pricing</span><span>Blog</span><span>FAQs</span><span>Support</span><span>Reviews</span><span>Contact Us</span>
  </nav>
</header>

<section class="hero">
  <div class="hero-art placeholder" role="img" aria-label="Illustration of a person filing folders into a large cabinet drawer on a laptop"></div>
  <div class="hero-copy">
    <div class="lead">Keeping track of all your</div>
    <h1>Paper documents &amp; other belongings</h1>
    <div class="accent">has never been easier!</div>
    <div class="hero-actions">
      <span class="btn">Free Trial</span>
      <span class="btn btn-ghost">Download App</span>
    </div>
  </div>
</section>

<section class="welcome">
  <div class="eyebrow">Find any document or item instantly</div>
  <h2>Welcome to Brisk find</h2>
  <p>Brisk Find is a system that allows you to quickly search for the location of every item that you store so far. It is an essential tool for keeping track of paper documents or any other kind of physical item. You'll have the ability to quickly find any item you're searching for, even when you've stored it there infrequently. Using Brisk Find helps you save considerable space without losing speedy accessibility to your treasured items.</p>
  <span class="btn">Read More</span>
</section>

<section class="pricing">
  <h2 class="section-title">Our Pricing Plans</h2>
  <p class="section-sub">Choose the plan that fits the way you store things, from a single cabinet to an entire office archive.</p>
  <div class="plans">
    <div class="plan"><h3>Starter Plan</h3><div class="price"><sup>$</sup>500</div><p>Ideal for small homes with a few boxes to track.</p><span class="btn btn-blue">Get Started</span></div>
    <div class="plan"><h3>Basic Plan</h3><div class="price"><sup>$</sup>1000</div><p>Great for families and small offices to organise.</p><span class="btn btn-blue">Get Started</span></div>
    <div class="plan"><h3>Basic Plan</h3><div class="price"><sup>$</sup>1500</div><p>Built for teams with large archives and storage.</p><span class="btn btn-blue">Get Started</span></div>
  </div>
</section>

<section class="blog">
  <h2 class="section-title">Lates Blog</h2>
  <div class="rule"></div>
  <p class="section-sub">Tips, stories and updates on keeping your papers and belongings in order, written by our team.</p>
  <div class="posts">
    <article class="post">
      <div class="post-img placeholder" role="img" aria-label="Photo of hands holding a smartphone at a desk" style="background:linear-gradient(135deg,#d9d4cc,#8d8a86)"></div>
      <div class="meta">By Admin · 5 January 2020</div>
      <h3>Lorem ipsum dolor sit amet ou pers dolore modre</h3>
      <p>Short notes on finding any stored paper in seconds, with simple labels and a quick search from your phone.</p>
      <span class="btn">Read More</span>
    </article>
    <article class="post">
      <div class="post-img placeholder" role="img" aria-label="Photo of people working together at a table" style="background:linear-gradient(135deg,#6b5a4a,#2f3440)"></div>
      <div class="meta">By Admin · 12 January 2020</div>
      <h3>Sum dolor sit amet ou per pours dolore modre</h3>
      <p>How small offices can track folders, boxes and shared equipment without losing hours each week.</p>
      <span class="btn">Read More</span>
    </article>
    <article class="post">
      <div class="post-img placeholder" role="img" aria-label="Photo of a smiling woman holding a phone" style="background:linear-gradient(135deg,#f2b84a,#8a5a3a)"></div>
      <div class="meta">By Admin · 20 January 2020</div>
      <h3>Porro dolore modre Lorem ipsum dolor sit ametou per</h3>
      <p>Everyday habits that keep your home archive tidy, searchable and ready whenever you need it.</p>
      <span class="btn">Read More</span>
    </article>
  </div>
</section>

<section class="app">
  <div class="app-copy">
    <h2>Download App</h2>
    <p>Keep your storage map in your pocket. Scan a label, add a photo and record where every item lives, then find it again with one quick search. Your records stay in sync across phone, tablet and desktop so the whole household or team always knows where things are kept.</p>
    <div class="stores">
      <span class="btn btn-ghost"><span class="store-dot"></span>Phone Store</span>
      <span class="btn btn-ghost"><span class="store-dot"></span>Droid Shelf</span>
      <span class="btn btn-ghost"><span class="store-dot"></span>Desktop Shop</span>
      <span class="btn">Try Free Trial</span>
    </div>
  </div>
  <div class="app-art placeholder" role="img" aria-label="Illustration of a smartphone with folders flying out of its screen"></div>
</section>

<section class="reviews">
  <h2 class="section-title">Customers Reviews</h2>
  <p class="section-sub">What people say after moving their paperwork and belongings into a single searchable place.</p>
  <svg class="arrow" style="left:90px" width="20" height="40" viewBox="0 0 20 40"><path d="M18 2 2 20l16 18" fill="none" stroke="#6b7480" stroke-width="2"/></svg>
  <svg class="arrow" style="right:90px" width="20" height="40" viewBox="0 0 20 40"><path d="M2 2l16 18L2 38" fill="none" stroke="#6b7480" stroke-width="2"/></svg>
  <div class="avatar placeholder" role="img" aria-label="Customer portrait"></div>
  <div class="reviewer">Owen Harlow</div>
  <div class="stars">
    <svg width="90" height="16" viewBox="0 0 90 16" fill="var(--orange)"><g id="s"><path d="M8 0l2.4 5 5.6.6-4.2 3.8 1.2 5.6L8 12.2 3 15l1.2-5.6L0 5.6 5.6 5z"/></g><use href="#s" x="18"/><use href="#s" x="36"/><use href="#s" x="54"/><use href="#s" x="72"/></svg>
  </div>
  <p class="quote">I used to spend ages hunting for receipts and warranty papers. Now every box in the attic is listed and I can find anything in a few seconds. Setup was simple and the app is a joy to use.</p>
  <div class="dots"><span class="on"></span><span></span><span></span><span></span><span></span><span></span></div>
</section>

<section class="faq">
  <h2 class="section-title">FAQs</h2>
  <div class="rule"></div>
  <div class="faq-grid">
    <div class="faq-col">
      <div class="faq-item">Q. LOREMIPSUM IS SIMPLY DUMMY TEXT?<span>+</span></div>
      <div class="faq-item">Q. LOREMIPSUM IS SIMPLY DUMMY TEXT?<span>+</span></div>
      <div class="faq-item">Q. LOREMIPSUM IS SIMPLY DUMMY TEXT?<span>+</span></div>
      <div class="faq-item">Q. LOREMIPSUM IS SIMPLY DUMMY TEXT?<span>+</span></div>
      <div class="faq-item">Q. LOREMIPSUM IS SIMPLY DUMMY TEXT?<span>+</span></div>
    </div>
    <div class="faq-col">
      <div class="faq-open">
        <h4>Q. LOREMIPSUM IS SIMPLY DUMMY TEXT?<span>−</span></h4>
        <p>Lorem ipsum dolor sit amet, consectetur adipiscing elit. Sed posuere dapibus tellus, vitae faucibus magna ultricies et. Donec euismod turpis vel ligula feugiat, nec commodo nulla pretium. Aliquam erat volutpat. Nulla facilisi. Curabitur vehicula, metus at sodales porta, lorem mauris tincidunt nisl, quis fermentum urna sem ut erat. Vivamus non magna vel enim laoreet posuere.</p>
      </div>
      <div class="faq-item">Q. LOREMIPSUM IS SIMPLY DUMMY TEXT?<span>+</span></div>
    </div>
  </div>
</section>

<section class="contact">
  <h2 class="section-title">Get in Touch</h2>
  <div class="rule"></div>
  <p class="section-sub">Questions about plans or setup? Send us a message and our team will reply within one business day.</p>
  <div class="form">
    <div class="form-col">
      <div class="field"><label>Name*</label><div class="line"></div></div>
      <div class="field"><label>Email*</label><div class="line"></div></div>
      <div class="field"><label>Phone*</label><div class="line"></div></div>
    </div>
    <div class="form-col">
      <div class="field"><label>Comment*</label><div class="area"></div></div>
    </div>
  </div>
  <span class="btn send">Send Message</span>
</section>

<footer class="site-footer">
  <div class="social"><span></span><span></span><span></span><span></span><span></span><span></span></div>
  <p class="copyright">© 2020 Company Name All Right Reserved</p>
</footer>

</body>
</html>
```